Velundra Jobs portal

Velundra Jobs is a job portal connecting job seekers and companies offering part time jobs in the Mena region, starting in the UAE. We would like to see designs that use the color blue. We have attached images to give an idea what the website should look like. When a company posts a job the job seekers are not allowed to see which company has posted a job. There should also be a coinvex gateway. On the landing page we want a catching picture that we will send.

Target Market(s)

Students and promotional workers

Logo Text

Velundra Jobs

Coding

Coded - Design and coding required

Number of Pages Required

4 page

Font styles to use
Sans Serif

Colors
33a6d7
0692cd
85cae6

```html
<!DOCTYPE html>
<html lang="en">
<head>
<meta charset="UTF-8">
<title>Velundra Jobs</title>
<link rel="stylesheet" href="https://fonts.googleapis.com/css2?family=Outfit:wght@300;400;600;700&family=Open+Sans:wght@400&display=swap">
<style>
  :root {
    --bar-top: #1fb3f7;
    --bar-bottom: #2f6dbf;
    --white: #ffffff;
    --logo-teal: #3cb6c4;
    --sky-light: #c9d9e0;
    --sky-mid: #9fc1d2;
    --sky-deep: #6f98ad;
    --join-top: #22aaf2;
    --join-bottom: #2f6dc1;
    --employer-top: #a9c51b;
    --employer-bottom: #7a960f;
    --seeker-top: #fa0a0a;
    --seeker-bottom: #b00000;
  }
  * { margin: 0; padding: 0; box-sizing: border-box; }
  html, body { width: 1200px; height: 658px; overflow: hidden; }
  body { position: relative; font-family: "Outfit", sans-serif; color: var(--white); }

  .top-bar {
    position: absolute; left: 0; top: 0; width: 1200px; height: 56px;
    background: linear-gradient(var(--bar-top), var(--bar-bottom));
    z-index: 2;
  }
  .account-links {
    position: absolute; right: 98px; top: 19px;
    font-family: "Open Sans", sans-serif; font-size: 12.5px;
    display: flex; gap: 12px;
  }
  .brand-box {
    position: absolute; left: 99px; top: 0; width: 155px; height: 189px;
    background: var(--white); z-index: 3;
    display: flex; flex-direction: column; align-items: center; justify-content: center; gap: 14px;
  }
  .brand-mark { width: 46px; height: 46px; border-radius: 50%; background: var(--logo-teal); }
  .brand-name {
    font-size: 24px; font-weight: 400; color: var(--logo-teal); line-height: 1.1; text-align: center;
  }

  .hero {
    position: absolute; left: 0; top: 56px; width: 1200px; height: 540px;
    background: linear-gradient(160deg, var(--sky-light) 0%, var(--sky-mid) 55%, var(--sky-deep) 100%);
  }
  .slide-arrow { position: absolute; top: 241px; }
  .slide-arrow.prev { left: 28px; }
  .slide-arrow.next { right: 36px; }

  .hero-title {
    position: absolute; left: 0; width: 1200px; top: 224px;
    text-align: center; font-size: 32px; font-weight: 600; letter-spacing: 0.2px;
    text-shadow: 0 1px 3px rgba(0,0,0,0.25);
  }
  .hero-lead {
    position: absolute; left: 0; width: 1200px; top: 286px;
    text-align: center; font-size: 19px; font-weight: 300; line-height: 25px;
  }
  .actions { position: absolute; left: 257px; top: 390px; display: flex; gap: 19px; }
  .action {
    width: 216px; height: 75px; border-radius: 3px;
    display: flex; align-items: center; justify-content: center;
    font-size: 21px; font-weight: 600; letter-spacing: 0.2px;
  }
  .action.join { background: linear-gradient(var(--join-top), var(--join-bottom)); }
  .action.employer { background: linear-gradient(var(--employer-top), var(--employer-bottom)); }
  .action.seeker { background: linear-gradient(var(--seeker-top), var(--seeker-bottom)); }

  .site-footer {
    position: absolute; left: 0; top: 596px; width: 1200px; height: 62px;
    background: linear-gradient(var(--bar-top), var(--bar-bottom));
    font-size: 12.5px;
  }
  .copyright { position: absolute; left: 99px; top: 24px; }
  .footer-links { position: absolute; right: 97px; top: 22px; }
</style>
</head>
<body>
  <header class="top-bar">
    <nav class="account-links"><span>Register</span><span>|</span><span>Login</span></nav>
  </header>

  <div class="brand-box">
    <div class="brand-mark"></div>
    <div class="brand-name">Velundra Jobs</div>
  </div>

  <section class="hero">
    <div class="hero-photo" role="img" aria-label="Photo of a young man in shirt and tie with arms spread wide against a cloudy blue sky and mountains" style="position:absolute;inset:0;"></div>
    <svg class="slide-arrow prev" width="32" height="66" viewBox="0 0 32 66"><polyline points="30,1 2,33 30,65" fill="none" stroke="#fff" stroke-width="2"/></svg>
    <svg class="slide-arrow next" width="32" height="66" viewBox="0 0 32 66"><polyline points="2,1 30,33 2,65" fill="none" stroke="#fff" stroke-width="2"/></svg>
    <h1 class="hero-title">WE ARE PROVIDING PART TIME JOBS FOR STUDENTS IN DUBAI</h1>
    <p class="hero-lead">It you are a student and have quite free time and want to invest it gaining<br>extra money ,so you are in the right place</p>
    <div class="actions">
      <div class="action join">JOIN VELUNDRA</div>
      <div class="action employer">EMPLOYER</div>
      <div class="action seeker">JOB SEEKER</div>
    </div>
  </section>

  <footer class="site-footer">
    <span class="copyright">Copyrights reserved to Velundra 2015</span>
    <span class="footer-links">About us - terms and conditionsv sitemap</span>
  </footer>
</body>
</html>
```